New web design for a service provider in the medical field

We are looking for a new design for our website. We are a company that repairs and sells medical endoscopes. Our customers include doctors and hospitals. Our current website can be found at https://lumavex.de/en/lumavex-english.
We need a new web design (without programming) for the following 3 pages:
-Startpage https://lumavex.de/en/lumavex-english/
-Used endoscopes https://lumavex.de/en/used-endoscopes/
-Purchase https://lumavex.de/en/purchase/
The design should be modern and stylish.
The blue color of the logo should be reflected on the page, but not too intrusive.
I have uploaded the images from the header. If more images are needed, let me know and I will upload them.

Target Market(s)
Doctors and hospitals

```html
<!DOCTYPE html>
<html lang="en">
<head>
<meta charset="utf-8">
<title>Lumavex – Used Endoscopes</title>
<link href="https://fonts.googleapis.com/css2?family=Barlow:wght@500;600;700&family=Roboto:wght@400;500&display=swap" rel="stylesheet">
<style>
:root{
  --blue:#1e9bd7;
  --blue-dark:#0b6fb8;
  --ink:#2f3338;
  --text:#666b72;
  --muted:#8a9097;
  --bg-soft:#e6f3f9;
  --white:#ffffff;
  --navy:#0d2a45;
  --line:#e3e8ec;
}
*{box-sizing:border-box;margin:0;padding:0}
html,body{width:1200px;height:3651px;overflow:hidden}
body{position:relative;font-family:"Roboto",sans-serif;color:var(--text);
  background:linear-gradient(180deg,#e3f1f8 0%,#eef7fb 30%,#e5f2f9 60%,#e9f5fa 89.7%,#ffffff 89.7%)}
.abs{position:absolute}
h1,h2,h3,h4{font-family:"Barlow",sans-serif;color:var(--ink);font-weight:600}
.accent{color:var(--blue)}
a{color:inherit;text-decoration:none}

/* top bar */
.topbar{top:0;left:0;width:1200px;height:44px;font-size:11px;color:#555}
.topbar .item{position:absolute;top:15px;display:flex;align-items:center;gap:6px}
.topbar svg{width:12px;height:12px;stroke:var(--blue);fill:none;stroke-width:1.5}
.social{display:flex;gap:16px}
.social span{width:8px;height:8px;border-radius:50%;background:#333;display:block}

/* nav */
.nav{top:44px;left:128px;width:943px;height:72px;background:var(--white);border-radius:6px;
  box-shadow:0 4px 20px rgba(30,100,150,.06);display:flex;align-items:center;padding:0 28px}
.brand{display:flex;align-items:center;gap:8px;font-family:"Barlow",sans-serif;font-weight:700;font-size:17px;color:var(--ink)}
.brand i{width:12px;height:12px;border-radius:50%;background:var(--blue);display:block}
.nav ul{list-style:none;display:flex;gap:26px;margin-left:auto;margin-right:26px;font-size:11.5px;color:#333}
.nav li.active{color:var(--blue)}
.btn{background:var(--blue-dark);color:#fff;border-radius:20px;font-size:11.5px;font-weight:500;padding:10px 26px}

/* hero */
.hero-title{top:225px;left:154px;font-size:38px;line-height:50px}
.hero-text{top:334px;left:156px;width:360px;font-size:11px;line-height:21px}
.hero-img{top:162px;left:630px;width:413px;height:280px;border:5px solid #fff;border-radius:10px;
  background:linear-gradient(135deg,#eceef1,#c9ced4 55%,#2d3238 85%);box-shadow:0 4px 18px rgba(0,0,0,.06)}

/* intro */
.eyebrow{font-size:14px;color:#444}
.intro{top:543px;left:156px;width:620px}
.intro h2{font-size:34px;line-height:49px;margin:8px 0 18px}
.intro p{font-size:11px;line-height:21.5px;margin-bottom:10px}
.intro h4{font-size:14px;margin:18px 0 12px;color:#333}
.features{top:519px;left:840px;width:204px;height:537px;background:#fff;border-radius:8px;
  display:flex;flex-direction:column;justify-content:space-around;padding:40px 0;text-align:center}
.feature svg{width:60px;height:60px;fill:none;stroke:var(--blue);stroke-width:2}
.feature h4{font-size:14.5px;margin:8px 0 6px}
.feature p{font-size:10.5px;color:var(--muted)}

/* section headings */
.sec-head{left:0;width:1200px;text-align:center}
.sec-head .eyebrow{font-size:13.5px}
.sec-head h2{font-size:36px;line-height:48px;margin-top:10px}
.sec-head p{width:680px;margin:22px auto 0;font-size:11px;line-height:21px}

/* product cards */
.card{width:402px;height:452px;background:#fff;border-radius:8px;overflow:hidden;box-shadow:0 4px 20px rgba(30,100,150,.05)}
.card .img{height:270px}
.card .body{padding:26px 32px}
.card h3{font-size:17px;font-weight:500;margin-bottom:10px}
.card p{font-size:10.5px;line-height:20px}
.brands{display:flex;gap:12px;margin-top:16px}
.brands span{font-family:"Barlow",sans-serif;font-size:10px;font-weight:700;padding:4px 10px;background:#f3f5f7;color:#333;border-radius:3px}
.more{display:flex;align-items:center;gap:14px;margin-top:22px;font-size:12px;font-weight:500;color:#333}
.more svg{width:16px;height:16px;stroke:var(--blue-dark);stroke-width:2;fill:none}

/* manufacturers */
.maker{top:2546px;width:200px;height:65px;background:#fff;border-radius:6px;display:flex;align-items:center;justify-content:center;
  font-family:"Barlow",sans-serif;font-weight:700;font-size:28px;color:var(--ink)}

/* reasons */
.reason{top:2910px;width:275px;height:203px;background:#fff;border-radius:8px;padding:26px 28px}
.reason svg{width:32px;height:32px;stroke:var(--blue);fill:none;stroke-width:2}
.reason h4{font-size:14.5px;margin:12px 0 8px}
.reason p{font-size:10.5px;line-height:20px}
.arrow{top:2996px;width:30px;height:30px;border-radius:50%;border:1px solid #aab;background:#fff;display:flex;align-items:center;justify-content:center}
.arrow svg{width:14px;height:14px;stroke:#333;fill:none;stroke-width:1.6}

/* cta */
.cta{top:3213px;left:128px;width:943px;height:132px;background:var(--blue-dark);border-radius:6px;color:#fff;padding:42px 35px}
.cta .eyebrow{color:#fff;font-size:14px}
.cta h2{color:#fff;font-size:34px;margin-top:4px}
.cta .btn-light{position:absolute;right:35px;top:48px;background:#fff;color:var(--blue-dark);border-radius:20px;font-size:11px;font-weight:500;padding:11px 36px}

/* footer */
.footer{top:3393px;left:156px;width:888px;font-size:10px;color:#555}
.footer h5{font-family:"Barlow",sans-serif;font-size:13px;font-weight:600;color:#333;margin-bottom:16px}
.footer ul{list-style:none;line-height:24.5px}
.col{position:absolute;top:0}
.contact{line-height:24px;margin-top:18px}
.news{display:flex;align-items:center;justify-content:space-between;width:222px;height:34px;border:1px solid var(--blue-dark);border-radius:18px;padding:0 3px 0 16px;margin-top:14px;color:#999;font-size:9px}
.news i{width:27px;height:27px;border-radius:50%;background:var(--blue-dark);display:block}
.bottom{top:3599px;left:0;width:1200px;height:52px;background:var(--navy);color:#dfe6ec;font-size:10px}
.bottom span{position:absolute;top:21px}
</style>
</head>
<body>

<div class="abs topbar">
  <div class="item" style="left:156px"><svg viewBox="0 0 12 12"><rect x="1" y="2.5" width="10" height="7"/><path d="M1 3l5 4 5-4"/></svg>info@lumavex.de</div>
  <div class="item" style="left:300px"><svg viewBox="0 0 12 12"><path d="M2 1.5l2.5 0 1 3-1.5 1a6 6 0 0 0 2.5 2.5l1-1.5 3 1v2.5c-5 0-8.5-3.5-8.5-8.5z"/></svg>+49 4000 555 120-0</div>
  <div class="item" style="left:608px">Pick Up Order</div>
  <div class="item" style="left:702px">About US</div>
  <div class="item" style="left:775px">Contact Us</div>
  <div class="item" style="left:873px"><span style="width:16px;height:10px;background:#2b3f8f;display:block"></span><span style="font-size:8px;color:#999">▾</span></div>
  <div class="item social" style="left:953px"><span></span><span></span><span></span><span></span></div>
</div>

<nav class="abs nav">
  <div class="brand"><i></i>Lumavex</div>
  <ul>
    <li>Home</li><li>Endoscope Repair</li><li class="active">Used Endoscopes</li><li>Endoscopy Systems</li><li>Endoscopy Accessories</li>
  </ul>
  <a class="btn" href="https://lumavex.de/en/purchase/">Purchase Now!</a>
</nav>

<h1 class="abs hero-title">Quality Without<br><span class="accent">Compromise</span></h1>
<p class="abs hero-text">Lorem ipsum dolor sit amet, consectetur adipiscing sed do eiusmod tempor incididunt ut labore et dolore amet magna aliqua.</p>
<div class="abs hero-img" role="img" aria-label="Photo of endoscope control handles hanging on a white rack"></div>

<section class="abs intro">
  <div class="eyebrow">Lorem Ipsum</div>
  <h2>Purchase of <span class="accent">Used Endoscopes</span><br>– The Inexpensive Alternative</h2>
  <p>Used endoscopes are an excellent, high-quality alternative to new equipment for all doctors and hospitals who want to add to their equipment pool cost-effectively. On our website you will find all types of equipment - gastroscopes, coloscopes, bronchoscopes, cystoscopes and duodenoscopes.</p>
  <p>All used endoscopes that we offer for sale were already in medical use and have been professionally looked after and serviced during this time. In addition, we can offer you endoscopy accessories both for medical examinations and for cleaning and maintaining your endoscopes.</p>
  <h4>Quality with warranty for more safety</h4>
  <p>After the purchase, our technicians subjected the devices to extensive technical tests and overhauled them. Last but not least, we rely on well-known brands that themselves stand for a high quality standard – Orbiscan, Veltrax and Kairon. For these reasons we can offer a twelve month warranty on our used equipment!</p>
  <p>Only tested quality leaves our company: To ensure the highest quality standards, we carry out an intensive outgoing inspection on every device before dispatch. We enclose documentation of the test result with your endoscope and archive it for future reference.</p>
</section>

<aside class="abs features">
  <div class="feature">
    <svg viewBox="0 0 60 60"><circle cx="30" cy="26" r="16"/><circle cx="30" cy="26" r="12"/><path d="M14 40h32l-4 6 4 6H14l4-6z"/><text x="30" y="30" text-anchor="middle" font-size="11" fill="#1e9bd7" stroke="none" font-family="Barlow">12</text></svg>
    <h4>12 months warranty</h4><p>Highest quality standards</p>
  </div>
  <div class="feature">
    <svg viewBox="0 0 60 60"><circle cx="30" cy="22" r="10"/><path d="M18 22a12 12 0 0 1 24 0M14 56c0-10 7-16 16-16s16 6 16 16z"/><path d="M40 26c0 4-4 6-8 6"/></svg>
    <h4>Best customer service</h4><p>We are there for you</p>
  </div>
  <div class="feature">
    <svg viewBox="0 0 60 60"><circle cx="30" cy="30" r="24"/><ellipse cx="30" cy="30" rx="10" ry="24"/><path d="M6 30h48M10 18h40M10 42h40"/></svg>
    <h4>Worldwide shipping</h4><p>Our service knows no borders!</p>
  </div>
</aside>

<header class="abs sec-head" style="top:1125px">
  <div class="eyebrow">Lorum Ipsum Dolor</div>
  <h2><span class="accent">Used</span> Device - <span class="accent">Fair</span> Price - <span class="accent">Full</span> Performance</h2>
  <p>Lorem ipsum dolor sit amet, consectetur adipiscing elit, sed do eiusmod tempor incididunt ut labore et dolore magna aliqua. Ut enim ad minim veniam, quis nostrud exercitation ullamco laboris nisi ut aliquip ex ea commodo consequat. Duis aute irure</p>
</header>

<article class="abs card" style="top:1299px;left:176px">
  <div class="img" role="img" aria-label="Photo of flexible video endoscopes hanging on a wall rack" style="background:linear-gradient(180deg,#e8ebee,#cfd4d8 60%,#3a3f45)"></div>
  <div class="body"><h3>Flexible Video Endoscopes</h3>
    <p>Discover our flexible endoscopes from the best brands such as Orbiscan, Veltrax and Kairon: gastroscopes, coloscopes, bronchoscopes, duodenoscopes, cystoscopes and more.</p>
    <div class="brands"><span>ORBISCAN</span><span>VELTRAX</span><span>KAIRON</span></div></div>
</article>
<article class="abs card" style="top:1299px;left:622px">
  <div class="img" role="img" aria-label="Photo of a video processor and light source unit" style="background:linear-gradient(135deg,#f2a07a,#e6e7ea 45%,#c8cdd3)"></div>
  <div class="body"><h3>Processors &amp; Light-Sources</h3>
    <p>Provide better diagnosis to your patients by means of high-resolution imaging, implemented by the best video processors of the latest generation.</p>
    <div class="brands"><span>ORBISCAN</span><span>VELTRAX</span><span>KAIRON</span></div></div>
</article>
<article class="abs card" style="top:1792px;left:176px">
  <div class="img" role="img" aria-label="Photo of a clinician working at an endoscopy system tower" style="background:linear-gradient(135deg,#d9dde1,#f0f1f3 50%,#b9c0c8)"></div>
  <div class="body"><h3>Endoscopy Systems</h3>
    <p>We help you with configuring a complete endoscopy system for your needs and requirements - from the endoscope to the peripheral devices (processor, light source, screen, suction pump, etc.).</p>
    <div class="more">Learn all about Endoscopy Systems<svg viewBox="0 0 16 16"><path d="M2 8h12M9 3l5 5-5 5"/></svg></div></div>
</article>
<article class="abs card" style="top:1792px;left:622px">
  <div class="img" role="img" aria-label="Photo of endoscopy accessories on a turquoise surface" style="background:linear-gradient(160deg,#e8a45a,#5fb6c4 45%,#3a9fb0)"></div>
  <div class="body"><h3>Accesories</h3>
    <p>Cover your needs for consumables for single or multiple specific use - from biopsy forceps to cleaning brushes and much more.</p>
    <div class="more">Find your accessories here!<svg viewBox="0 0 16 16"><path d="M2 8h12M9 3l5 5-5 5"/></svg></div></div>
</article>

<header class="abs sec-head" style="top:2327px">
  <div class="eyebrow">Lorem Ipsum Dolor</div>
  <h2>Second Hand Endoscopes From<br><span class="accent">Leading Manufacturers</span></h2>
  <p>Discover our range of second hand and refurbished endoscopes from leading manufacturers.<br>We give a twelve month warranty for this.</p>
</header>
<div class="abs maker" style="left:259px">Orbiscan</div>
<div class="abs maker" style="left:500px">Veltrax</div>
<div class="abs maker" style="left:740px">Kairon</div>

<header class="abs sec-head" style="top:2690px">
  <div class="eyebrow">Lorem Ipsum Dolor</div>
  <h2>We are Your First Choice When Buying<br><span class="accent">Used Endoscopy Equipment</span></h2>
  <p>Lorem ipsum dolor sit amet, consectetur adipiscing elit, sed do eiusmod tempor incididunt ut labore et dolore magna aliqua. Ut enim ad minim veniam, quis nostrud exercitation ullamco laboris nisi ut aliquip ex ea commodo consequat. Duis aute irure</p>
</header>
<div class="abs arrow" style="left:113px"><svg viewBox="0 0 14 14"><path d="M12 7H2M6 3L2 7l4 4"/></svg></div>
<div class="abs arrow" style="left:1057px"><svg viewBox="0 0 14 14"><path d="M2 7h10M8 3l4 4-4 4"/></svg></div>
<div class="abs reason" style="left:156px">
  <svg viewBox="0 0 32 32"><circle cx="16" cy="16" r="5"/><path d="M16 3v5M16 24v5M3 16h5M24 16h5M7 7l3.5 3.5M21.5 21.5L25 25M7 25l3.5-3.5M21.5 10.5L25 7"/></svg>
  <h4>As New Equipment</h4>
  <p>The devices have already been in medical use before but were professionally maintained and serviced. Consumable parts were completely renewed after purchase by ...</p>
</div>
<div class="abs reason" style="left:463px">
  <svg viewBox="0 0 32 32"><circle cx="16" cy="16" r="13"/><path d="M12 23V9h5a4 4 0 0 1 0 8h-5M16 17l5 6"/></svg>
  <h4>Brand Manufacturers</h4>
  <p>We primarily offer the brands Orbiscan, Veltrax and Kairon, which are characterized by long-lasting quality and whose manufacturers have already earned ...</p>
</div>
<div class="abs reason" style="left:768px">
  <svg viewBox="0 0 32 32"><circle cx="13" cy="13" r="9"/><path d="M20 20l9 9"/></svg>
  <h4>Tested &amp; Overhauled</h4>
  <p>Our trained technicians have checked and overhauled every device in a variety of ways before it is offered for resale.</p>
</div>

<section class="abs cta">
  <div class="eyebrow">Get In Touch</div>
  <h2>How Can We Help You?</h2>
  <a class="btn-light" href="https://lumavex.de/en/lumavex-english/">Contact Us Now</a>
</section>

<footer class="abs footer" style="height:170px">
  <div class="col" style="left:0">
    <div class="brand" style="margin-top:10px"><i></i>Lumavex</div>
    <div class="contact">+49 4000 555 120-0<br>info@lumavex.de</div>
    <div class="social" style="margin-top:12px"><span></span><span></span><span></span><span></span></div>
  </div>
  <div class="col" style="left:274px"><h5>Quick Links</h5>
    <ul><li>Home</li><li>Endoscope Repair</li><li>Used Endoscopes</li><li>Endoscopy Systems</li><li>Endoscopy Accessories</li></ul></div>
  <div class="col" style="left:505px"><h5>Usefull Links</h5>
    <ul><li>Information</li><li>About Us</li><li>Contact Us</li><li>TOS</li><li>FAQ</li></ul></div>
  <div class="col" style="left:664px;width:224px"><h5>Newsletter</h5>
    <p style="line-height:19px">Lorem ipsum dolor sit consectetur adipiscing elit sed do eiusmod tempor incididunt ut labore et dolore magna aliqua.</p>
    <div class="news">Your Email<i></i></div></div>
</footer>

<div class="abs bottom">
  <span style="left:156px">2022 All rights reserved</span>
  <span style="left:856px">Privacy Policy</span>
  <span style="left:955px">Terms &amp; Conditions</span>
</div>

</body>
</html>
```